Business Cards for IT Consulting Company (Managed Service Provider)

I am looking to have some business cards printed and would like some designs. We are an IT Consulting company based in Vancouver BC. I would like a nice clean and modern look to the cards. I have uploaded all the versions of my logo so parts can be used as needed. Here is a snippit from our website homepage:

Quillbrook Networks Ltd. is an IT Solutions Partner located in Vancouver BC, Canada. We offer IT solutions and support to customers in the greater Vancouver Area. With expertise in Microsoft platforms, as well as Linux and Mac OSX and over 12 years experience in the IT industry, Quillbrook Networks is dedicated to offering our clients top quality service and products. We take pride in the solutions we offer our customers. The greatest compliment a client can give us is to recommend our services.

Quillbrook Networks Ltd. offers a wide range of IT services from onsite service to remote support and managed service solutions. This allows clients to choose the support path that best suits their company’s needs. Supporting many different sized companies from small to enterprise level over the past 12 years Quillbrook Networks has the experience and expertise needed to ensure things run smoothly. Allowing our clients to focus on doing business.

Revolutionizing the way IT services are delivered.

Quillbrook Networks is dedicated to providing our clients with IT solutions that work and grow with them for years to come. This philosophy helps save money in the long run instead of replacing equipment constantly. Far too often IT solutions are not well thought out and while possibly solving the problem at hand, require replacement due to growth or quality within a very short time frame. Quillbrook Networks takes pride in providing solutions that will last and be able to accommodate growth without the need for replacement.

Industry/Entity Type

Information Technology

Contact Information for Business Card

Quillbrook Networks Ltd.
(Employee Name)
Eml: (Employees Email Address)
Web: quillbrook.me
Ph: 604-555-0148

Font styles to use
Serif
Sans Serif

Requirements
Must have
• The Company logo and company colors.
Nice to have
• - Our tag line: "Reinventing Your IT Services" or "Revolutionizing the way IT services are delivered."
• - Also I really like the idea of nature and technology together blending which is sort of where my logo came from so integrating that somehow onto the business cards would be great.

```html
<!DOCTYPE html>
<html lang="en">
<head>
<meta charset="utf-8">
<title>Quillbrook Networks Ltd. – Business Card</title>
<link rel="stylesheet" href="https://fonts.googleapis.com/css2?family=Montserrat:wght@400;500&family=Source+Sans+3:wght@400;600&display=swap">
<style>
  :root {
    --stage: #000000;
    --brand-blue: #0ba0d9;
    --card-light: #f3f3f3;
    --ink-grey: #58595b;
    --white: #ffffff;
  }
  * { box-sizing: border-box; margin: 0; padding: 0; }
  html, body {
    width: 1200px;
    height: 900px;
    overflow: hidden;
    background: var(--stage);
  }
  .stage {
    position: relative;
    width: 1200px;
    height: 900px;
    background: var(--stage);
  }
  .card {
    position: absolute;
    top: 200px;
    width: 310px;
    height: 502px;
  }
  .card--front {
    left: 265px;
    background: var(--card-light);
    border-radius: 56px 0 56px 0;
  }
  .card--back {
    left: 641px;
    width: 309px;
    background: var(--brand-blue);
    border-radius: 0 56px 0 56px;
  }

  /* Front: wordmark */
  .wordmark {
    position: absolute;
    left: 86px;
    top: 52px;
    color: var(--brand-blue);
    font-family: "Montserrat", sans-serif;
    font-weight: 500;
    line-height: 1;
  }
  .wordmark__mark {
    position: absolute;
    left: -66px;
    top: 6px;
    width: 46px;
    height: 46px;
    border: 2px solid var(--brand-blue);
  }
  .wordmark__name { display: block; font-size: 36px; letter-spacing: -0.5px; }
  .wordmark__sub { display: block; font-size: 14px; letter-spacing: 0.4px; margin-top: 3px; }

  /* Front: person + contact */
  .person {
    position: absolute;
    left: 29px;
    top: 366px;
    font-family: "Source Sans 3", sans-serif;
    font-weight: 600;
    font-size: 19px;
    color: var(--ink-grey);
  }
  .person__first { color: var(--brand-blue); }
  .contact {
    position: absolute;
    left: 29px;
    top: 414px;
    list-style: none;
    font-family: "Source Sans 3", sans-serif;
    font-size: 14.5px;
    color: var(--ink-grey);
  }
  .contact__item {
    display: flex;
    align-items: center;
    height: 21px;
  }
  .contact__icon {
    width: 10px;
    height: 10px;
    margin-right: 5px;
    fill: var(--brand-blue);
  }

  /* Back */
  .back-field {
    position: absolute;
    inset: 0;
    border-radius: inherit;
    background: var(--brand-blue);
  }
  .back-brand {
    position: absolute;
    left: 33px;
    top: 346px;
    color: var(--white);
    font-family: "Montserrat", sans-serif;
    font-weight: 500;
    line-height: 1;
  }
  .back-brand__name { display: block; font-size: 46px; letter-spacing: -0.5px; }
  .back-brand__sub { display: block; font-size: 17px; letter-spacing: 0.5px; margin-top: 2px; }
  .tagline {
    position: absolute;
    left: 0;
    width: 309px;
    top: 428px;
    text-align: center;
    color: var(--white);
    font-family: "Source Sans 3", sans-serif;
    font-weight: 600;
    font-size: 16px;
  }
</style>
</head>
<body>
<main class="stage">
  <section class="card card--front">
    <div class="wordmark">
      <span class="wordmark__mark"></span>
      <span class="wordmark__name">quillbrook</span>
      <span class="wordmark__sub">NETWORKS LTD.</span>
    </div>

    <p class="person"><span class="person__first">Daniel</span> Porter</p>

    <ul class="contact">
      <li class="contact__item">
        <svg class="contact__icon" viewBox="0 0 10 10" aria-hidden="true">
          <path d="M2 0.5 L3.6 2.6 L2.8 3.7 C3.4 5 4.8 6.5 6.3 7.2 L7.4 6.4 L9.5 8 L8.4 9.5 C4.5 9.2 0.8 5.5 0.5 1.6 Z"/>
        </svg>
        604-555-0148
      </li>
      <li class="contact__item">
        <svg class="contact__icon" viewBox="0 0 10 10" aria-hidden="true">
          <path d="M0 2 H10 V8.5 H0 Z M0.8 2.6 L5 5.6 L9.2 2.6" stroke="#f3f3f3" stroke-width="0.8"/>
        </svg>
        info@quillbrook.me
      </li>
      <li class="contact__item">
        <svg class="contact__icon" viewBox="0 0 10 10" aria-hidden="true">
          <circle cx="5" cy="5" r="4.6"/>
          <path d="M3 3 Q4.5 2.5 5 4 Q4 5.5 3.2 5 Z M6 6 Q7.5 5.8 7.6 7.2 Q6.6 8 6 6 Z" fill="#f3f3f3"/>
        </svg>
        www.quillbrook.me
      </li>
    </ul>
  </section>

  <section class="card card--back">
    <div class="back-field" role="img" aria-label="Faint tonal geometric brand pattern across the blue field"></div>
    <div class="back-brand">
      <span class="back-brand__name">quillbrook</span>
      <span class="back-brand__sub">NETWORKS LTD.</span>
    </div>
    <p class="tagline">Reinventing Your IT Services</p>
  </section>
</main>
</body>
</html>
```